Dunmore Roofing

Want a professional looking business card

Industry/Entity Type

Business

Contact Information for Business Card

Paul Dunmore ( Owner) paul@dunmoreroofing-example.com, www.dunmoreroofing-example.com, Adress: 4172 Township road 43 Ashcombe Glen,XN K9X4T2

```html
<!DOCTYPE html>
<html lang="en">
<head>
<meta charset="utf-8">
<title>Dunmore Roofing – Business Card</title>
<link rel="stylesheet" href="https://fonts.googleapis.com/css2?family=Oswald:wght@600&family=Ubuntu:wght@400;500&display=swap">
<style>
  :root {
    --backdrop: #161616;
    --card: #262626;
    --card-edge: #2e2e2e;
    --accent: #234a96;
    --text-light: #f2f2f2;
    --logo-silver: #d4d4d4;
  }
  * { box-sizing: border-box; margin: 0; padding: 0; }
  html, body {
    width: 1200px; height: 900px; overflow: hidden;
    background: var(--backdrop);
    font-family: "Ubuntu", sans-serif;
  }
  .canvas {
    width: 1200px; height: 900px;
    display: flex; flex-direction: column; align-items: center;
    justify-content: center; gap: 28px;
  }
  .card {
    position: relative;
    width: 660px; height: 377px;
    background: linear-gradient(135deg, var(--card) 0%, var(--card-edge) 100%);
    overflow: hidden;
  }
  .card__band {
    position: absolute; left: 0; right: 0; bottom: 0;
    height: 7px; background: var(--accent);
  }
  /* Front */
  .brand {
    position: absolute; left: 0; right: 0; top: 140px;
    display: flex; align-items: center; justify-content: center; gap: 14px;
  }
  .brand__mark {
    width: 22px; height: 22px; background: var(--logo-silver);
  }
  .brand__name {
    font-family: "Ubuntu", sans-serif; font-weight: 500;
    font-size: 38px; letter-spacing: 1px; color: var(--logo-silver);
    white-space: nowrap;
  }
  .front__web {
    position: absolute; left: 0; right: 0; bottom: 34px;
    text-align: center; font-size: 14px; letter-spacing: 0.5px;
    color: var(--text-light);
  }
  .hl { color: var(--accent); }
  /* Back */
  .identity {
    position: absolute; top: 146px; left: 20px; width: 272px;
    text-align: right;
  }
  .identity__name {
    font-family: "Oswald", sans-serif; font-weight: 600;
    font-size: 36px; line-height: 1; color: var(--accent);
    text-transform: uppercase; letter-spacing: 0.5px;
    white-space: nowrap;
  }
  .identity__role {
    margin-top: 6px; font-size: 20px; color: var(--text-light);
  }
  .divider {
    position: absolute; left: 312px; top: 142px;
    width: 2px; height: 78px; background: var(--accent);
  }
  .contacts {
    position: absolute; left: 334px; top: 146px;
    list-style: none; display: flex; flex-direction: column; gap: 6px;
  }
  .contacts__item {
    display: flex; align-items: center; gap: 12px;
    font-size: 14.5px; letter-spacing: 0.4px; color: var(--text-light);
    white-space: nowrap;
  }
  .contacts__item svg { width: 14px; height: 14px; flex: none; }
  .address {
    position: absolute; left: 70px; bottom: 34px;
    display: flex; align-items: center; gap: 12px;
    font-size: 16px; letter-spacing: 0.5px; color: var(--text-light);
    white-space: nowrap;
  }
  .address svg { width: 18px; height: 18px; flex: none; }
</style>
</head>
<body>
<main class="canvas">
  <section class="card card--front">
    <div class="brand">
      <span class="brand__mark"></span>
      <span class="brand__name">Dunmore Roofing</span>
    </div>
    <p class="front__web">www.<span class="hl">dunmoreroofing-example</span>.com</p>
    <div class="card__band"></div>
  </section>

  <section class="card card--back">
    <div class="identity">
      <h1 class="identity__name">Paul Dunmore</h1>
      <p class="identity__role">Owner</p>
    </div>
    <div class="divider"></div>
    <ul class="contacts">
      <li class="contacts__item">
        <svg viewBox="0 0 14 14"><rect x="3.5" y="1" width="7" height="12" rx="1.2" fill="none" stroke="#234a96" stroke-width="1.4"/><line x1="6" y1="11" x2="8" y2="11" stroke="#234a96" stroke-width="1.2"/></svg>
        <span>(000)123-4567</span>
      </li>
      <li class="contacts__item">
        <svg viewBox="0 0 14 14"><rect x="1" y="3" width="12" height="8.5" fill="#234a96"/><polyline points="1,3 7,8 13,3" fill="none" stroke="#262626" stroke-width="1.2"/></svg>
        <span>paul@dunmoreroofing-example.com</span>
      </li>
      <li class="contacts__item">
        <svg viewBox="0 0 14 14"><circle cx="6" cy="6" r="4" fill="none" stroke="#234a96" stroke-width="1.8"/><line x1="9" y1="9" x2="13" y2="13" stroke="#234a96" stroke-width="2"/></svg>
        <span>www.<span class="hl">dunmoreroofing-example</span>.com</span>
      </li>
    </ul>
    <p class="address">
      <svg viewBox="0 0 18 18"><polygon points="17,1 1,8 8,10 10,17" fill="#f2f2f2"/></svg>
      <span>4172 Township road 43 Ashcombe Glen,XN K9X4T2</span>
    </p>
    <div class="card__band"></div>
  </section>
</main>
</body>
</html>
```